Animal Eye Clinic needs a Business card

We are a new veterinary ophthalmology practice (Ridgeline Pet Vision Care) and we need a business card designed. We only see animal eyes - we are not a regular veterinary clinic. We already have a logo. We are looking for a professional, good looking business card to hand out to our clients. We are looking for something simple but professional and contemporary. Our logo is likely the only picture/graphic that needs to be on the card.
Updates

Contact Information for Business Card

Delia Vossman, BSc, DVM, MSc, DipACVO
Veterinary Ophthalmologist

Phone: 250.418.3927
Email: ridgelinepetvisioncare@mailbox-example.net
Website: ridgelinepetvisioncare-example.net
Address: 1874 Thornbury Rd
Kelowna, BC, V1X 4M9

Colors

Designer to choose colors to be used in the design.

Requirements
Must have
• Our logo (attached)

```html
<!DOCTYPE html>
<html lang="en">
<head>
<meta charset="utf-8">
<title>Ridgeline Pet Vision Care – Business Card</title>
<link href="https://fonts.googleapis.com/css2?family=Lato:wght@400;700;900&display=swap" rel="stylesheet">
<style>
  :root {
    --bg: #e9ecee;
    --teal-light: #00e2ea;
    --teal: #00b3bd;
    --teal-deep: #007c8e;
    --white: #ffffff;
    --ink: #3a3a3a;
    --grey: #5b5b5b;
  }
  * { box-sizing: border-box; margin: 0; padding: 0; }
  html, body {
    width: 1200px; height: 960px; overflow: hidden;
    background: var(--bg);
    font-family: "Lato", sans-serif;
  }
  .canvas {
    width: 1200px; height: 960px;
    display: flex; flex-direction: column;
    align-items: center; justify-content: center; gap: 56px;
  }
  .card {
    width: 700px; height: 400px;
    border-radius: 22px;
    overflow: hidden;
    position: relative;
    box-shadow: 0 6px 18px rgba(0,0,0,0.12);
  }
  /* Front */
  .card-front {
    background: linear-gradient(135deg, var(--teal-light) 0%, var(--teal) 55%, var(--teal-deep) 130%);
    display: flex; align-items: center; justify-content: center;
  }
  .brand {
    display: flex; align-items: center; gap: 18px;
    color: var(--white);
  }
  .brand-dot {
    width: 58px; height: 58px; border-radius: 50%;
    background: var(--white);
    flex: none;
  }
  .brand-name {
    font-weight: 900;
    font-size: 34px;
    letter-spacing: 0.5px;
    text-transform: uppercase;
    line-height: 1.1;
  }
  /* Back */
  .card-back {
    background: var(--white);
  }
  .animal-art {
    position: absolute; left: 0; bottom: 0;
    width: 330px; height: 330px;
  }
  .details {
    position: absolute; right: 40px; top: 40px;
    text-align: right;
  }
  .person-name {
    color: var(--teal);
    font-weight: 900;
    font-size: 22px;
    letter-spacing: 0.3px;
    text-transform: uppercase;
  }
  .credentials {
    color: var(--teal);
    font-weight: 900;
    font-size: 17px;
    text-transform: uppercase;
    margin-top: 2px;
  }
  .role {
    color: var(--grey);
    font-size: 16px;
    margin-top: 4px;
  }
  .contact {
    position: absolute; right: 40px; bottom: 40px;
    text-align: right;
    color: var(--ink);
    font-size: 16px;
    line-height: 1.45;
  }
  .phone {
    font-size: 30px;
    font-weight: 400;
    letter-spacing: 0.5px;
    margin-bottom: 4px;
  }
</style>
</head>
<body>
<main class="canvas">
  <section class="card card-front">
    <div class="brand">
      <span class="brand-dot"></span>
      <span class="brand-name">Ridgeline Pet<br>Vision Care</span>
    </div>
  </section>

  <section class="card card-back">
    <svg class="animal-art" viewBox="0 0 330 330" role="img" aria-label="Illustration of horse, dog and cat head silhouettes in teal, white and grey">
      <defs>
        <linearGradient id="artTeal" x1="0" y1="0" x2="1" y2="1">
          <stop offset="0" stop-color="#00c4cd"/>
          <stop offset="1" stop-color="#007c8e"/>
        </linearGradient>
      </defs>
      <path d="M0 0 H250 Q330 120 300 330 H0 Z" fill="url(#artTeal)"/>
    </svg>

    <div class="details">
      <p class="person-name">Delia Vossman</p>
      <p class="credentials">BSc, DVM, MSc, DipACVO</p>
      <p class="role">Veterinary Ophthalmologist</p>
    </div>

    <div class="contact">
      <p class="phone">250.418.3927</p>
      <p>ridgelinepetvisioncare@mailbox-example.net</p>
      <p>www.ridgelinepetvisioncare-example.net</p>
      <p>1874 Thornbury Rd, Kelowna, BC, V1X 4M9</p>
    </div>
  </section>
</main>
</body>
</html>
```